DeskHarbor - Coworking website design

DeskHarbor is a new global coworking brand, growing fast and establishing stylish locations and communities that inspire innovation and collaboration all around the world.
The project includes a complete website design, focused on delivering the company’s values and messages, provide information to site visitors and to generate leads.

Please review the attached design brief, for more information.

Target Market(s)

Both men and women. Decision makers in:
Small & medium businesses in various fields, but mainly technology firms (Startups or established brands).
Global enterprises.
Dynamic “new generation” companies.
Press

Number of Pages Required

2 page

Requirements
Must have
• Project Scope & deliverables:
• Concept and design for :
• Home page
• Deliver the values mentioned above.
• Showcase the cities in which the company has locations in.
• Show customer testimonials.
• Provide an interface (form) for booking a tour and/or leaving contact details for more information (two alternatives)
• Coworking location page - Each location is in the coolest part of a different major city, and has its own address, set of amenities (kitchen, fast internet etc,), area information (public transportation accessibility, sites near by, bars and restaurants in walking distance) and pricing for private offices (based on number of people per office). Each location page must have an interface to book a location tour.
• Site Navigation (header & footer) - allow simple navigation between multiple city pages, location pages and homepage. Growth of up to 50 locations in 25 cities.
• The navigation should account for Navigation to additional pages (not commissioned in this project) such as:
• Locations
• Enterprise
• Special promotions
• Blog
• Contact us
• About us
• Note - the site should account for geolocation variable display, showing different content for different locations.
• Deliverables must include all editable graphic files (photoshop or similar), as follows:
• Home page - Desktop view (preferably both)
• Location page - Mobile web view (preferably both)
• Navigation - both options

```html
<!DOCTYPE html>
<html lang="en">
<head>
<meta charset="utf-8">
<title>DeskHarbor – Coworking</title>
<link rel="stylesheet" href="https://fonts.googleapis.com/css2?family=Playfair+Display:wght@400;700&family=Montserrat:wght@400;500;600&display=swap">
<style>
:root{
  --black:#000;
  --ink:#111;
  --text:#222;
  --muted:#444;
  --white:#fff;
  --band:#ececec;
  --panel:#141414;
  --tab-grey:#6e6e6e;
  --btn-grey:#6b6b6b;
  --photo-light:#d9dcdf;
  --photo-mid:#a9adb1;
  --photo-dark:#4d4f52;
  --map:#c9c9c9;
}
*{box-sizing:border-box;margin:0;padding:0}
html,body{width:1200px;height:3488px;overflow:hidden}
body{position:relative;background:var(--white);font-family:"Montserrat",sans-serif;color:var(--text)}
.abs{position:absolute}
.serif{font-family:"Playfair Display",serif}
.btn{position:absolute;display:flex;align-items:center;justify-content:center;background:var(--black);color:var(--white);border-radius:24px;font-family:"Playfair Display",serif;font-weight:700}
.btn-sm{width:114px;height:36px;font-size:13px}
.copy{font-size:13px;line-height:21px;color:var(--text)}
.card-title{font-size:21px;font-weight:500;color:var(--ink)}

/* header */
.site-header{left:0;top:0;width:1200px;height:93px;background:var(--black)}
.brand{left:107px;top:20px;font-size:43px;color:var(--white)}
.main-nav{right:102px;top:38px;display:flex;gap:34px;font-size:15px;color:var(--white)}

/* hero */
.hero{left:0;top:93px;width:1200px;height:570px;background:linear-gradient(180deg,#f4f5f6 0%,#d8dbde 45%,#b5b8bb 80%,#c9cbcd 100%)}
.hero-curve{left:0;top:93px}
.hero-title{left:150px;top:246px;width:900px;text-align:center;font-size:36px;line-height:48px;color:var(--ink)}
.hero .btn{left:420px;top:302px;width:172px;height:52px;font-size:20px}

/* welcome */
.welcome-title{left:100px;top:710px;font-size:21px;font-weight:700;color:var(--ink)}
.welcome-sub{left:100px;top:746px;font-size:15px;color:var(--ink)}
.welcome-copy{left:100px;top:786px;width:530px;text-align:justify}
.welcome .btn{left:100px;top:922px}
.circle-photo{left:691px;top:677px;width:386px;height:386px;border-radius:50%;background:linear-gradient(160deg,#1a1a1a 0%,#1a1a1a 14%,#dfe3e6 15%,#b7bcc0 55%,#3c3e40 100%)}

/* projects band */
.band{left:0;top:1086px;width:1200px;height:896px;background:var(--band)}
.projects{left:100px;top:1119px;width:605px;height:293px}
.projects-label{left:0;top:0;width:214px;height:293px;background:var(--black);color:var(--white);padding:46px 0 0 30px}
.projects-label h2{font-size:30px;font-weight:400}
.projects-label p{font-size:13px;margin-top:8px}
.projects-photo{left:214px;top:0;width:391px;height:293px;background:linear-gradient(135deg,#5b5c5e,#9c9a95 50%,#3d3e40)}
.tile{width:212px;height:251px}
.tile-a{left:493px;top:1428px;background:linear-gradient(160deg,#c4c4c2,#7e7c78 55%,#3e3d3b)}
.tile-b{left:98px;top:1691px;background:linear-gradient(150deg,#8a6a4e,#c9a57e 50%,#4b3a2c)}
.feature{width:370px}
.feature .copy{margin-top:18px}
.feature .btn{position:relative;margin-top:16px}

/* testimonials */
.testi-title{left:0;top:2030px;width:1200px;text-align:center;font-size:21px;font-weight:700;color:var(--ink)}
.testi{width:244px}
.testi-head{display:flex;align-items:center;gap:14px}
.avatar{width:72px;height:72px;border-radius:50%;background:radial-gradient(circle at 50% 40%,#c9a58a,#6b4a36)}
.testi-name{font-size:21px;color:var(--ink)}
.testi-role{font-size:12px;color:var(--muted);margin-top:2px}
.testi p{margin-top:16px;font-size:12.5px;line-height:20px;text-align:justify;color:var(--text)}
.dots{left:552px;top:2336px;display:flex;gap:14px}
.dots span{width:22px;height:3px;background:var(--black)}
.dots span.off{background:#ccc}

/* booking */
.tab{top:2391px;height:61px;display:flex;align-items:center;font-size:17px;color:var(--white)}
.tab-book{left:98px;width:207px;background:var(--black);padding-left:42px}
.tab-contact{left:305px;width:226px;padding-left:46px}
.tab-contact svg{position:absolute;left:0;top:0}
.tab-contact span{position:relative}
.booking{left:98px;top:2452px;width:1000px;height:251px;background:linear-gradient(135deg,#1b1b1b,#0e0e0e 60%,#1d1d1d)}
.field{width:240px;height:32px;background:var(--white);border-radius:3px;display:flex;align-items:center;justify-content:space-between;padding:0 14px;font-size:13px;color:#666}
.field i{width:0;height:0;border-left:5px solid transparent;border-right:5px solid transparent;border-top:6px solid #333}
.book-now{left:542px;top:2623px;width:116px;height:32px;border-radius:16px;background:var(--btn-grey);color:var(--white);font-family:"Playfair Display",serif;font-weight:700;font-size:13px;display:flex;align-items:center;justify-content:center}

/* locations */
.locations{left:0;top:2733px;width:1200px;height:551px;background:var(--band)}
.loc-title{left:0;top:2783px;width:1200px;text-align:center;font-size:21px;font-weight:700;color:var(--ink)}
.world-map{left:100px;top:2840px;width:970px;height:416px;background:radial-gradient(ellipse at 50% 45%,#d2d2d2 0%,#c4c4c4 55%,rgba(236,236,236,0) 72%)}

/* footer */
.footer-nav{left:0;top:3330px;width:1200px;display:flex;justify-content:center;gap:32px;font-size:14px;color:var(--ink)}
.social{left:0;top:3383px;width:1200px;display:flex;justify-content:center;gap:36px}
.social span{width:16px;height:16px;border-radius:50%;background:var(--ink)}
.copyright{left:0;top:3424px;width:1200px;text-align:center;font-size:11px;color:var(--muted)}
.footer-bar{left:0;top:3477px;width:1200px;height:11px;background:var(--black)}
</style>
</head>
<body>

<header class="abs site-header">
  <div class="abs brand serif">DeskHarbor</div>
  <nav class="abs main-nav">
    <span>Locations</span><span>Enterprise</span><span>Special promotions</span><span>Blog</span><span>Contact us</span><span>About us</span>
  </nav>
</header>

<section class="abs hero" role="img" aria-label="Bright open-plan office with desks, chairs and city views"></section>
<svg class="abs hero-curve" width="1200" height="570" viewBox="0 0 1200 570" aria-hidden="true">
  <path d="M0 570 Q600 470 1200 570 Z" fill="#fff"/>
</svg>
<section class="abs" style="left:0;top:93px;width:1200px;height:570px">
  <h1 class="abs hero-title serif" style="top:153px;font-weight:400">DeskHarbor is focused on a stylish work environment that includes private offices, with shared lounges, meeting rooms and kitchens</h1>
  <div class="btn" style="left:514px;top:302px;width:172px;height:52px;font-size:20px">Read more</div>
</section>

<section class="welcome">
  <h2 class="abs welcome-title serif">Welcome To Our Website</h2>
  <div class="abs welcome-sub">About Coworking</div>
  <p class="abs welcome-copy copy">Coworking is a style of work that involves a shared working environment. Unlike in a typical office environment, those coworking are usually employed by various organizations. Coworking is a gathering of a group of people who are working independently, but who share values, and who are interested in the synergy that can happen from working with like-minded people. Coworking is not only about the physical place, but about establishing and being part of a community.</p>
  <div class="btn btn-sm" style="left:100px;top:922px">Read more</div>
  <div class="abs circle-photo" role="img" aria-label="Colleagues gathered around a desk in a modern office"></div>
</section>

<section class="abs band"></section>
<div class="abs projects">
  <div class="abs projects-label">
    <h2 class="serif">Our Projects</h2>
    <p>Values to deliver</p>
  </div>
  <div class="abs projects-photo" role="img" aria-label="Team working together over plans on a large table"></div>
</div>

<div class="abs feature" style="left:735px;top:1176px">
  <h3 class="card-title">Inspire collaboration &amp; Innovation</h3>
  <p class="copy">Lorem ipsum dolor sit amet, consectetur adipiscing elit, sed do eiusmod tempor incididunt ut labore et dolore magna aliqua. Ut enim ad minim veniam, quis nostrud exercitation ullamco laboris nisi ut aliquip ex ea commodo consequat.</p>
  <div class="btn btn-sm">Read more</div>
</div>

<div class="abs feature" style="left:98px;top:1464px">
  <h3 class="card-title">Idea sharing</h3>
  <p class="copy">Lorem ipsum dolor sit amet, consectetur adipiscing elit, sed do eiusmod tempor incididunt ut labore et dolore magna aliqua. Ut enim ad minim veniam, quis nostrud exercitation ullamco laboris nisi ut aliquip ex ea commodo consequat.</p>
  <div class="btn btn-sm">Read more</div>
</div>
<div class="abs tile tile-a" role="img" aria-label="Group of coworkers talking in a bright brick-walled space"></div>
<div class="abs feature" style="left:740px;top:1464px">
  <h3 class="card-title">Be a part of an exclusive club</h3>
  <p class="copy">Lorem ipsum dolor sit amet, consectetur adipiscing elit, sed do eiusmod tempor incididunt ut labore et dolore magna aliqua. Ut enim ad minim veniam, quis nostrud exercitation ullamco laboris nisi ut aliquip ex ea commodo consequat.</p>
  <div class="btn btn-sm">Read more</div>
</div>

<div class="abs tile tile-b" role="img" aria-label="Two colleagues sharing a tablet at a table"></div>
<div class="abs feature" style="left:344px;top:1734px">
  <h3 class="card-title">Realize your greatness</h3>
  <p class="copy">Lorem ipsum dolor sit amet, consectetur adipiscing elit, sed do eiusmod tempor incididunt ut labore et dolore magna aliqua. Ut enim ad minim veniam, quis nostrud exercitation ullamco laboris nisi ut aliquip ex ea commodo consequat.</p>
  <div class="btn btn-sm">Read more</div>
</div>
<div class="abs feature" style="left:740px;top:1734px">
  <h3 class="card-title">Style and design awareness</h3>
  <p class="copy">Lorem ipsum dolor sit amet, consectetur adipiscing elit, sed do eiusmod tempor incididunt ut labore et dolore magna aliqua. Ut enim ad minim veniam, quis nostrud exercitation ullamco laboris nisi ut aliquip ex ea commodo consequat.</p>
  <div class="btn btn-sm">Read more</div>
</div>

<h2 class="abs testi-title serif">Testimonials</h2>
<div class="abs testi" style="left:179px;top:2100px">
  <div class="testi-head"><div class="avatar" role="img" aria-label="Client portrait"></div><div><div class="testi-name">Mara Quill</div><div class="testi-role">Description</div></div></div>
  <p>Pellentesque habitant morbi tristique senectus et netus et malesuada fames ac turpis egestas. Vestibulum tortor quam, feugiat vitae, ultricies eget, tempor sit amet, ante.</p>
</div>
<div class="abs testi" style="left:479px;top:2100px">
  <div class="testi-head"><div class="avatar" role="img" aria-label="Client portrait"></div><div><div class="testi-name">Lena Whitcombe</div><div class="testi-role">Description</div></div></div>
  <p>Pellentesque habitant morbi tristique senectus et netus et malesuada fames ac turpis egestas. Vestibulum tortor quam, feugiat vitae, ultricies eget, tempor sit amet, ante.</p>
</div>
<div class="abs testi" style="left:779px;top:2100px">
  <div class="testi-head"><div class="avatar" role="img" aria-label="Client portrait"></div><div><div class="testi-name">Tobias</div><div class="testi-role">Description</div></div></div>
  <p>Pellentesque habitant morbi tristique senectus et netus et malesuada fames ac turpis egestas. Vestibulum tortor quam, feugiat vitae, ultricies eget, tempor sit amet, ante.</p>
</div>
<div class="abs dots"><span></span><span class="off"></span><span></span></div>

<div class="abs tab tab-book">Booking a Tour</div>
<div class="abs tab tab-contact">
  <svg width="226" height="61" viewBox="0 0 226 61" aria-hidden="true"><path d="M0 0 H196 L226 61 H0 Z" fill="#6e6e6e"/></svg>
  <span>Quick Contact</span>
</div>
<section class="abs booking">
  <div class="abs field" style="left:135px;top:51px">Location From<i></i></div>
  <div class="abs field" style="left:381px;top:51px">Location To<i></i></div>
  <div class="abs field" style="left:630px;top:51px">No of person<i></i></div>
  <div class="abs field" style="left:135px;top:98px">Date From<i></i></div>
  <div class="abs field" style="left:381px;top:98px">Date To<i></i></div>
  <div class="abs field" style="left:630px;top:98px">Rooms<i></i></div>
</section>
<div class="abs book-now">Book Now</div>

<section class="abs locations"></section>
<h2 class="abs loc-title serif">Our Locations</h2>
<div class="abs world-map" role="img" aria-label="Grey world map showing company locations"></div>
<svg class="abs" style="left:0;top:2733px" width="1200" height="551" viewBox="0 0 1200 551" aria-hidden="true">
  <g fill="#111">
    <path d="M442 137 c-6 0 -10 4 -10 9 c0 7 10 17 10 17 s10 -10 10 -17 c0 -5 -4 -9 -10 -9z"/>
    <path d="M270 197 c-6 0 -10 4 -10 9 c0 7 10 17 10 17 s10 -10 10 -17 c0 -5 -4 -9 -10 -9z"/>
    <path d="M812 200 c-6 0 -10 4 -10 9 c0 7 10 17 10 17 s10 -10 10 -17 c0 -5 -4 -9 -10 -9z"/>
    <path d="M689 256 c-6 0 -10 4 -10 9 c0 7 10 17 10 17 s10 -10 10 -17 c0 -5 -4 -9 -10 -9z"/>
    <path d="M840 260 c-6 0 -10 4 -10 9 c0 7 10 17 10 17 s10 -10 10 -17 c0 -5 -4 -9 -10 -9z"/>
    <path d="M398 338 c-6 0 -10 4 -10 9 c0 7 10 17 10 17 s10 -10 10 -17 c0 -5 -4 -9 -10 -9z"/>
    <path d="M930 410 c-6 0 -10 4 -10 9 c0 7 10 17 10 17 s10 -10 10 -17 c0 -5 -4 -9 -10 -9z"/>
    <path d="M614 290 c-11 0 -19 8 -19 17 c0 13 19 33 19 33 s19 -20 19 -33 c0 -9 -8 -17 -19 -17z M614 301 a6 6 0 1 1 0 12 a6 6 0 1 1 0 -12z" fill-rule="evenodd"/>
  </g>
</svg>

<footer>
  <nav class="abs footer-nav"><span>Locations</span><span>Enterprise</span><span>Special promotions</span><span>Blog</span><span>Contact us</span><span>About us</span></nav>
  <div class="abs social"><span></span><span></span><span></span><span></span></div>
  <div class="abs copyright">Copyrights © 2017 - All Rights Reserved</div>
  <div class="abs footer-bar"></div>
</footer>

</body>
</html>
```